Heron Property Inspection business card

I am the principal inspector of Heron Property Inspections. I serve Northern Virginia from Winchester to Arlington.Associate, Federated Guild of Dwelling Examiners (FGDE)Graduate, FGDE Home Inspectors CourseNational Association of Home Inspectors ExamI'd like the business card to look more professional than comical.I pulled the attached picture off the web. I'd like to have something like that or an image of a house as my logo on the cards.

Target Market(s)

Persons who recently purchased a home.

Industry/Entity Type

Business

Contact Information for Business Card

Bob AllenBadger Home Inspections, LLC.4455 River RoadBluemont, Virginia 20135cell: 703-231-6680e-mail: tkmarlow@postvale.net

Font styles to use
Serif
Sans Serif

Requirements
Must have
• I'd like to have a logo, something that identifies me as a home inspector. The attached images are something that I'd like to have incorporated into my business card logo.
Nice to have
• I'd like a sketch of a house and/or a magnifying glass showing a house being inspected. The attached images are used as a suggestion only, I do not own the images.
Should not have
• Gimmicky stuff. I want to appear professional and trustworthy.

```html
<!DOCTYPE html>
<html lang="en">
<head>
<meta charset="utf-8">
<title>Heron Property Inspections – Business Card</title>
<link rel="stylesheet" href="https://fonts.googleapis.com/css2?family=Marcellus&display=swap">
<style>
  :root {
    --bg: #2b2b2d;
    --brand-red: #9c1a20;
    --brand-red-light: #ad1f25;
    --brand-red-dark: #85141a;
    --ink: #3a3a3c;
    --paper: #ffffff;
    --font-main: "Marcellus", "Optima", serif;
  }
  html, body {
    margin: 0;
    padding: 0;
    width: 1200px;
    height: 1189px;
    overflow: hidden;
    background: var(--bg);
    font-family: var(--font-main);
  }
  .canvas {
    position: relative;
    width: 1200px;
    height: 1189px;
  }
  .card {
    position: absolute;
    left: 150px;
    width: 900px;
    height: 514px;
    border-radius: 26px;
    overflow: hidden;
    box-sizing: border-box;
  }
  /* Front side */
  .card--front {
    top: 55px;
    background: radial-gradient(circle at 50% 48%, var(--brand-red-light) 0%, var(--brand-red) 55%, var(--brand-red-dark) 100%);
    display: flex;
    align-items: center;
    justify-content: center;
  }
  .front-wordmark {
    color: var(--paper);
    font-size: 54px;
    line-height: 1.15;
    text-align: center;
    letter-spacing: 1px;
  }
  /* Back side */
  .card--back {
    top: 620px;
    background: var(--paper);
    color: var(--ink);
  }
  .back-wordmark {
    position: absolute;
    left: 80px;
    top: 150px;
    font-size: 38px;
    line-height: 1.15;
    color: var(--ink);
    letter-spacing: 0.5px;
  }
  .divider {
    position: absolute;
    left: 80px;
    top: 262px;
    width: 560px;
    height: 1px;
    background: var(--brand-red);
  }
  .person {
    position: absolute;
    right: 70px;
    top: 150px;
    text-align: right;
  }
  .person__name {
    font-size: 34px;
    color: var(--ink);
    letter-spacing: 1px;
  }
  .person__title {
    font-size: 20px;
    color: var(--brand-red);
    margin-top: 2px;
    letter-spacing: 1px;
  }
  .address {
    position: absolute;
    right: 70px;
    top: 300px;
    text-align: right;
    font-size: 27px;
    line-height: 1.25;
    color: var(--ink);
    letter-spacing: 0.5px;
  }
  .contact {
    position: absolute;
    left: 80px;
    top: 370px;
    list-style: none;
    margin: 0;
    padding: 0;
  }
  .contact__item {
    display: flex;
    align-items: center;
    font-size: 29px;
    color: var(--ink);
    margin-bottom: 10px;
    letter-spacing: 0.5px;
  }
  .contact__icon {
    width: 34px;
    height: 34px;
    margin-right: 18px;
    flex: none;
  }
</style>
</head>
<body>
<main class="canvas">
  <section class="card card--front" aria-label="Card front">
    <div class="front-wordmark">Heron Property<br>Inspections, LLC</div>
  </section>

  <section class="card card--back" aria-label="Card back">
    <div class="back-wordmark">Heron Property<br>Inspections, LLC</div>
    <div class="divider"></div>

    <div class="person">
      <div class="person__name">Employee Name</div>
      <div class="person__title">Managing Director</div>
    </div>

    <address class="address" style="font-style:normal">
      7182 Quarry Lane<br>Fernhill, Virginia 20148
    </address>

    <ul class="contact">
      <li class="contact__item">
        <svg class="contact__icon" viewBox="0 0 34 34" aria-hidden="true">
          <rect width="34" height="34" rx="6" fill="var(--brand-red)"/>
          <rect x="11" y="6" width="12" height="22" rx="2" fill="none" stroke="#fff" stroke-width="2"/>
          <rect x="13.5" y="9" width="7" height="5" fill="#fff"/>
          <circle cx="14" cy="18" r="1" fill="#fff"/><circle cx="17" cy="18" r="1" fill="#fff"/><circle cx="20" cy="18" r="1" fill="#fff"/>
          <circle cx="14" cy="21.5" r="1" fill="#fff"/><circle cx="17" cy="21.5" r="1" fill="#fff"/><circle cx="20" cy="21.5" r="1" fill="#fff"/>
        </svg>
        703-555-0192
      </li>
      <li class="contact__item">
        <svg class="contact__icon" viewBox="0 0 34 34" aria-hidden="true">
          <rect width="34" height="34" rx="6" fill="var(--brand-red)"/>
          <rect x="6" y="10" width="22" height="15" fill="none" stroke="#fff" stroke-width="2"/>
          <polyline points="6,10 17,19 28,10" fill="none" stroke="#fff" stroke-width="2"/>
        </svg>
        tkmarlow@postvale.net
      </li>
    </ul>
  </section>
</main>
</body>
</html>
```